Banner Ad Designs for tick and flea products

We sell tick and flea products online and want some great banner designs for our online website to promote our tick and flea products.

The ads must be made up in both Flash and HTML5
Ads can be formatted as .JPEG or .GIF files.

Please see the following url for creative requirements
http://help.bannerkite.com/creative-requirements/

Creative licence no limits to your imagination!

Ads must be created in the following sizes:

- Banner – 468×60
- Square – 250×250
- Small Square – 200×200
- Leaderboard – 728×90
- Medium Rectangle – 300×250
- Chatterly – 100×72

please view our website at www.globalpawstore.com.au or .com to get a feel for our website.

The aim is to attract customers who want to save on tick and flea purchases for their pets (dogs and cats)

Target Market(s)

Anyone who owns a dog or cat

Industry/Entity Type

Online

Font styles to use
Sans Serif
Other font styles liked:
• creative licence on font styles

Requirements
Must have
• Must have a strong urge to entice customers to click through.

Images wording and text etc use creative lic
Nice to have
• Strong appeal to dog and cat owners and how they can save on flea and tick essentials.
Keep it simple but effective.
Be fun and playful and inviting.
Should not have
• Please do not use words like cheap - cheapest

Strobing & Flashing - Strobing, flashing backgrounds, or otherwise distracting ads are not allowed. Do not attempt to overtly distract the user from page content.

```html
<!DOCTYPE html>
<html lang="en">
<head>
<meta charset="utf-8">
<title>Tick and Flea Banner Concepts</title>
<link href="https://fonts.googleapis.com/css2?family=Lato:wght@400;700&display=swap" rel="stylesheet">
<style>
  :root {
    --page: #ffffff;
    --leaf: #86ae33;
    --leaf-edge: #a3c95a;
    --cloud: #ffffff;
    --ink: #ffffff;
    --brand: #1f3f6e;
    --brand-dot: #2a7fc0;
    --label: #111111;
    --button-top: #8fe06a;
    --button-bottom: #2fa51f;
    --button-ink: #1c4a12;
    --badge: #cfe6fb;
    --badge-edge: #7fb3e3;
    --badge-ink: #2b4f9a;
    --photo-a: #d9cdb8;
    --photo-b: #7a6650;
    --photo-c: #2b2119;
  }
  html, body {
    margin: 0;
    width: 1200px;
    height: 900px;
    overflow: hidden;
    background: var(--page);
    font-family: "Lato", sans-serif;
  }
  .canvas { position: relative; width: 1200px; height: 900px; }
  .banner {
    position: absolute;
    top: 178px;
    width: 318px;
    height: 318px;
    box-sizing: border-box;
    background: var(--leaf);
    border: 2px solid var(--leaf-edge);
    box-shadow: inset 0 0 0 4px var(--leaf), inset 0 0 0 5px rgba(255,255,255,0.35);
    overflow: hidden;
  }
  .banner--a { left: 74px; }
  .banner--b { left: 440px; }
  .banner--c { left: 816px; }
  .cloud { position: absolute; left: 0; top: 0; width: 318px; height: 318px; }
  .pet-photo {
    position: absolute;
    left: 190px;
    top: 178px;
    width: 126px;
    height: 138px;
    background: radial-gradient(ellipse at 40% 60%, var(--photo-a) 0%, var(--photo-b) 55%, var(--photo-c) 100%);
    border-radius: 50% 40% 0 0;
  }
  .headline {
    position: absolute;
    left: 0;
    right: 0;
    margin: 0;
    color: var(--ink);
    font-weight: 700;
    font-size: 30px;
    line-height: 42px;
    text-align: center;
    letter-spacing: -0.2px;
  }
  .banner--a .headline { top: 6px; padding-left: 40px; padding-right: 8px; }
  .banner--b .headline, .banner--c .headline { top: 81px; }
  .brand {
    position: absolute;
    left: 16px;
    top: 262px;
    display: flex;
    align-items: center;
    gap: 6px;
    color: var(--brand);
    font-weight: 700;
    font-size: 17px;
    white-space: nowrap;
  }
  .brand__dot { width: 14px; height: 14px; border-radius: 50%; background: var(--brand-dot); }
  .order-button {
    position: absolute;
    left: 75px;
    top: 138px;
    width: 165px;
    height: 43px;
    box-sizing: border-box;
    border: 1px solid #1f7a14;
    border-radius: 4px;
    background: linear-gradient(var(--button-top), var(--button-bottom));
    color: var(--button-ink);
    font-weight: 700;
    font-size: 22px;
    line-height: 41px;
    text-align: center;
  }
  .shipping-badge { position: absolute; left: 225px; top: 4px; width: 84px; height: 84px; }
  .label {
    position: absolute;
    font-size: 54px;
    color: var(--label);
    font-weight: 400;
    transform: translate(-50%, -50%);
  }
</style>
</head>
<body>
<main class="canvas">
  <section class="banner banner--a">
    <svg class="cloud" viewBox="0 0 318 318" aria-hidden="true">
      <defs><filter id="soft-a"><feGaussianBlur stdDeviation="4"/></filter></defs>
      <path d="M0,318 L0,238 C25,215 65,210 95,224 C115,192 155,186 180,202 C205,162 262,150 318,166 L318,318 Z" fill="var(--cloud)" filter="url(#soft-a)"/>
    </svg>
    <div class="pet-photo" role="img" aria-label="Photo of a tabby cat lying beside a small black and tan dog"></div>
    <h2 class="headline">Save on<br>genuine brand<br>tick and flea<br>products</h2>
    <div class="brand"><span class="brand__dot"></span>Global Paw Store</div>
  </section>

  <section class="banner banner--b">
    <svg class="cloud" viewBox="0 0 318 318" aria-hidden="true">
      <defs><filter id="soft-b"><feGaussianBlur stdDeviation="4"/></filter></defs>
      <path d="M0,318 L0,238 C25,215 65,210 95,224 C115,192 155,186 180,202 C205,162 262,150 318,166 L318,318 Z" fill="var(--cloud)" filter="url(#soft-b)"/>
    </svg>
    <div class="pet-photo" role="img" aria-label="Photo of a tabby cat lying beside a small black and tan dog"></div>
    <h2 class="headline">Protect Your Pets!</h2>
    <div class="brand"><span class="brand__dot"></span>Global Paw Store</div>
  </section>

  <section class="banner banner--c">
    <svg class="cloud" viewBox="0 0 318 318" aria-hidden="true">
      <defs><filter id="soft-c"><feGaussianBlur stdDeviation="4"/></filter></defs>
      <path d="M0,318 L0,238 C25,215 65,210 95,224 C115,192 155,186 180,202 C205,162 262,150 318,166 L318,318 Z" fill="var(--cloud)" filter="url(#soft-c)"/>
    </svg>
    <div class="pet-photo" role="img" aria-label="Photo of a tabby cat lying beside a small black and tan dog"></div>
    <h2 class="headline">Save with us</h2>
    <div class="order-button">ORDER NOW</div>
    <svg class="shipping-badge" viewBox="0 0 84 84" aria-label="Free shipping badge">
      <polygon fill="var(--badge)" stroke="var(--badge-edge)" stroke-width="1.5"
        points="42,2 49,14 62,7 63,21 78,20 72,33 83,42 72,51 78,64 63,63 62,77 49,70 42,82 35,70 22,77 21,63 6,64 12,51 1,42 12,33 6,20 21,21 22,7 35,14"/>
      <text x="42" y="38" text-anchor="middle" font-family="Lato, sans-serif" font-weight="700" font-size="14" fill="var(--badge-ink)" transform="rotate(-15 42 42)">Free</text>
      <text x="42" y="54" text-anchor="middle" font-family="Lato, sans-serif" font-weight="700" font-size="12" fill="var(--badge-ink)" transform="rotate(-15 42 42)">Shipping</text>
    </svg>
    <div class="brand"><span class="brand__dot"></span>Global Paw Store</div>
  </section>

  <span class="label" style="left:167px; top:570px;">A</span>
  <span class="label" style="left:567px; top:558px;">B</span>
  <span class="label" style="left:973px; top:567px;">C</span>
</main>
</body>
</html>
```